Marlowby Services Website Design

We have most content but require a professional design. We have a logo already and will need it utilized along with several of the photos from the attached documentation.
First page should have our mission and Vision and the synapsis provided in the word document. Visitors will be prompted to select from one of our 3 divisions from this page.
Each division will have the same list of tabs : About, Services, Safety, Careers and Contact.
Photos on each divisions page should be representative of the divisions offerings. The word doc attached contains the requested content and we are open to edits that would complement and fill the website.
I like the Quorvane site www.quorvane.example - they are our competition so cant be modeled directly after this.
Please include prompts to request quote at each service page. align the format of the geotechnical page to the other 2 divisions.
I used chat gpt for some of the content so will need it optimized for SCO.

```html
<!DOCTYPE html>
<html lang="en">
<head>
<meta charset="utf-8">
<title>Marlowby Services</title>
<link href="https://fonts.googleapis.com/css2?family=Michroma&family=Roboto:wght@400;500;700&display=swap" rel="stylesheet">
<style>
:root{
  --red:#ee1c24;
  --black:#000;
  --white:#fff;
  --ink:#1b1b1b;
  --text:#3a3a3a;
  --grey-bg:#f4f4f4;
  --head:"Michroma",sans-serif;
  --body:"Roboto",sans-serif;
}
*{box-sizing:border-box;margin:0;padding:0}
html,body{width:1200px;height:3237px;overflow:hidden;background:var(--white);font-family:var(--body);color:var(--ink)}
.page{position:relative;width:1200px;height:3237px;overflow:hidden}

/* top bar */
.topbar{position:absolute;top:0;left:0;width:1200px;height:48px}
.topbar svg{position:absolute;inset:0}
.topbar .socials{position:absolute;left:554px;top:7px;display:flex;gap:9px}
.dot{width:34px;height:34px;border-radius:50%;background:var(--white)}
.topbar .mail{position:absolute;left:748px;top:14px;color:var(--white);font-size:15px;font-weight:500;display:flex;gap:10px;align-items:center}
.topbar .phone{position:absolute;left:972px;top:14px;color:var(--white);font-size:15px;font-weight:500;display:flex;gap:10px;align-items:center}

/* header */
.header{position:absolute;top:48px;left:0;width:1200px;height:106px}
.brand{position:absolute;left:112px;top:14px;font-family:var(--head);font-size:34px;color:var(--red);letter-spacing:1px}
.nav{position:absolute;left:448px;top:44px;display:flex;gap:31px;font-size:15px;font-weight:500}
.quote-btn{position:absolute;left:924px;top:30px;width:164px;height:48px;background:var(--red);color:var(--white);font-size:14px;font-weight:500;display:flex;align-items:center;justify-content:center}

/* hero + vision */
.hero{position:absolute;top:154px;left:0;width:1200px;height:937px}
.hero-photo{position:absolute;inset:0;height:660px;background:linear-gradient(180deg,#c9ccd0 0%,#8d8a7e 25%,#5c5a4c 55%,#3f3d35 100%)}
.hero svg{position:absolute;inset:0}
.welcome{position:absolute;left:110px;top:194px;color:var(--white);font-family:var(--head);font-size:27px}
.welcome-big{position:absolute;left:108px;top:226px;color:var(--white);font-family:var(--head);font-size:68px}
.vision{position:absolute;left:0;top:740px;width:1200px;text-align:center;color:var(--white)}
.vision h2{font-family:var(--head);font-size:32px;font-weight:400}
.rule{display:block;width:76px;height:4px;background:var(--white);margin:10px auto 0}
.vision p{margin:26px auto 0;width:840px;font-size:19px;font-weight:500;line-height:30px}

/* section titles */
.section-title{position:absolute;left:0;width:1200px;text-align:center;font-family:var(--head);font-size:32px;font-weight:400;color:var(--black)}
.section-title .rule{background:var(--red);margin-top:6px}

/* services */
.arrow{position:absolute;top:1388px;width:26px;height:26px;border-radius:50%;background:#fde8e8}
.arrow svg{width:26px;height:26px}
.card{position:absolute;width:303px;background:var(--white);box-shadow:0 0 14px rgba(238,28,36,.14)}
.card .img{margin:6px;height:211px}
.svc-label{position:absolute;top:1476px;height:75px;border-left:2px solid var(--red);padding:54px 0 0 22px;font-size:19px;font-weight:500;white-space:nowrap}

/* mission */
.mission{position:absolute;top:1666px;left:0;width:1200px;height:531px;background:var(--grey-bg)}
.mission svg{position:absolute;inset:0}
.mission-body{position:absolute;left:634px;top:62px;width:455px}
.mission-body h2{font-family:var(--head);font-size:36px;font-weight:400;color:var(--black)}
.mission-body .rule{position:absolute;left:-34px;top:60px;width:76px;height:4px;background:var(--red)}
.mission-body p{margin-top:20px;font-size:15.5px;line-height:25.7px;color:var(--text);text-align:justify}
.mission-body p+p{margin-top:12px}
.contact-btn{display:inline-flex;margin-top:28px;width:122px;height:48px;background:var(--red);color:var(--white);font-size:14px;font-weight:500;align-items:center;justify-content:center}

/* divisions */
.div-label{text-align:center;font-size:17px;font-weight:500;padding:24px 0 28px}

/* footer */
.footer{position:absolute;top:2770px;left:0;width:1200px;height:467px}
.footer svg{position:absolute;inset:0}
.fcol{position:absolute;top:170px;color:var(--white)}
.fcol h3{font-size:17px;font-weight:700;margin-bottom:16px}
.fcol li{list-style:none;font-size:14px;display:flex;align-items:center;gap:18px;height:39.5px}
.bullet{width:12px;height:12px;border-radius:50%;background:var(--red);position:relative}
.bullet:after{content:"";position:absolute;left:3px;top:4px;border-left:6px solid var(--black);border-top:2px solid transparent;border-bottom:2px solid transparent}
.info{display:flex;gap:20px;margin-bottom:14px}
.info svg{position:static;width:14px;height:14px;margin-top:2px}
.info b{display:block;font-size:14px;margin-bottom:4px}
.info span{display:block;font-size:11.5px;line-height:20px}
.fbrand{position:absolute;left:784px;top:232px;width:304px;text-align:center;font-family:var(--head);font-size:36px;color:var(--red)}
.fsocial{position:absolute;left:876px;top:310px;display:flex;gap:9px}
.fsocial .dot{width:34px;height:34px}
.fsocial .dot.red{background:var(--red)}
.fline{position:absolute;left:110px;top:404px;width:978px;height:1px;background:#333}
.copy{position:absolute;left:0;top:425px;width:1200px;text-align:center;color:var(--white);font-size:12px}
</style>
</head>
<body>
<div class="page">

  <div class="topbar">
    <svg width="1200" height="48" viewBox="0 0 1200 48">
      <polygon points="494,0 1200,0 1200,48 530,48" fill="var(--red)"/>
      <polygon points="940,0 1200,0 1200,48 918,48" fill="var(--black)"/>
      <line x1="690" y1="48" x2="722" y2="8" stroke="#fff" stroke-width="1.2"/>
      <line x1="700" y1="48" x2="732" y2="8" stroke="#fff" stroke-width="1.2"/>
    </svg>
    <div class="socials"><span class="dot"></span><span class="dot"></span><span class="dot"></span></div>
    <div class="mail">
      <svg width="15" height="12" viewBox="0 0 15 12"><rect width="15" height="12" rx="1" fill="#fff"/><path d="M0 1 7.5 7 15 1" stroke="var(--red)" stroke-width="1.5" fill="none"/></svg>
      info@marlowby.example
    </div>
    <div class="phone">
      <svg width="14" height="14" viewBox="0 0 24 24"><path fill="#fff" d="M6.6 10.8a15 15 0 0 0 6.6 6.6l2.2-2.2a1 1 0 0 1 1-.25 11.4 11.4 0 0 0 3.6.57 1 1 0 0 1 1 1V20a1 1 0 0 1-1 1A17 17 0 0 1 3 4a1 1 0 0 1 1-1h3.5a1 1 0 0 1 1 1c0 1.25.2 2.45.57 3.57a1 1 0 0 1-.25 1z"/></svg>
      555.014.8100
    </div>
  </div>

  <header class="header">
    <div class="brand">MARLOWBY</div>
    <nav class="nav"><span>ABOUT</span><span>SERVICES</span><span>SAFETY</span><span>CAREERS</span><span>CONTACT</span></nav>
    <div class="quote-btn">REQUEST A QUOTE</div>
  </header>

  <section class="hero">
    <div class="hero-photo" role="img" aria-label="Aerial view of a prairie town with a boom truck raising a worker beside a company sign"></div>
    <svg width="1200" height="937" viewBox="0 0 1200 937">
      <polygon points="0,462 898,650 1200,462 1200,937 0,937" fill="#fff"/>
      <polygon points="0,494 898,660 1200,494 1200,937 0,937" fill="var(--red)"/>
    </svg>
    <div class="welcome">WELCOME TO</div>
    <div class="welcome-big">MARLOWBY</div>
    <div class="vision">
      <h2>OUR VISION</h2>
      <span class="rule"></span>
      <p>To be the leading provider of aerial access, geotechnical drilling, and service solutions, setting the standard for excellence in safety, efficiency, and environmental stewardship.</p>
    </div>
  </section>

  <h2 class="section-title" style="top:1203px">MARLOWBY SERVICES<span class="rule"></span></h2>

  <div class="arrow" style="left:45px"><svg viewBox="0 0 26 26"><path d="M16 6 9 13l7 7" stroke="var(--red)" stroke-width="3" fill="none"/></svg></div>
  <div class="arrow" style="left:1126px"><svg viewBox="0 0 26 26"><path d="M10 6l7 7-7 7" stroke="var(--red)" stroke-width="3" fill="none"/></svg></div>

  <div class="card" style="left:112px;top:1288px;height:223px"><div class="img" role="img" aria-label="White boom truck parked in front of a rural building" style="background:linear-gradient(180deg,#9ab5cf 0%,#6c8a5a 35%,#d7d8d6 60%,#7c7460 100%)"></div></div>
  <div class="card" style="left:449px;top:1288px;height:223px"><div class="img" role="img" aria-label="Boom truck on a gravel yard at a construction site" style="background:linear-gradient(180deg,#4d5c3e 0%,#8a8f7d 40%,#b9b3a6 70%,#a59d8f 100%)"></div></div>
  <div class="card" style="left:785px;top:1288px;height:223px"><div class="img" role="img" aria-label="Boom truck on a forest road for utility work" style="background:linear-gradient(180deg,#3f5a2d 0%,#6f8f47 40%,#8a8676 75%,#6e6454 100%)"></div></div>

  <div class="svc-label" style="left:134px">DELIVERING SAFE</div>
  <div class="svc-label" style="left:470px">CONSTRUCTION</div>
  <div class="svc-label" style="left:806px">UTILITY</div>

  <section class="mission">
    <svg width="1200" height="531" viewBox="0 0 1200 531">
      <defs><linearGradient id="sky" x1="0" y1="0" x2="0" y2="1"><stop offset="0" stop-color="#2b6fc9"/><stop offset=".55" stop-color="#86ade0"/><stop offset=".75" stop-color="#d6d9dc"/><stop offset="1" stop-color="#777"/></linearGradient></defs>
      <polygon points="0,0 437,0 598,531 0,531" fill="url(#sky)" role="img" aria-label="Boom truck parked in front of a water tower"/>
      <polygon points="437,0 444,0 636,531 598,531" fill="var(--red)"/>
    </svg>
    <div class="mission-body">
      <h2>OUR MISSION</h2>
      <span class="rule"></span>
      <p>At Marlowby, our mission is to deliver unparalleled aerial access, geotechnical drilling, and service and maintenance solutions, consistently exceeding our clients' expectations. We strive to achieve this by investing in cutting-edge technology, fostering a culture of safety and continuous improvement, and prioritizing environmental sustainability.</p>
      <p>Through collaboration, integrity, and dedication, we aim to contribute to the success of our clients while maintaining the highest standards of quality and professionalism.</p>
      <span class="contact-btn">CONTACT US</span>
    </div>
  </section>

  <h2 class="section-title" style="top:2316px">SELECT DIVISION<span class="rule"></span></h2>

  <div class="card" style="left:112px;top:2405px"><div class="img" role="img" aria-label="Aerial view of a town with a raised boom and sign" style="background:linear-gradient(180deg,#a9a59a 0%,#8c8a80 50%,#6f7068 100%)"></div><div class="div-label">AERIAL ACCESS</div></div>
  <div class="card" style="left:449px;top:2405px"><div class="img" role="img" aria-label="Boom truck reaching up a tall white tower under blue sky" style="background:linear-gradient(180deg,#2f78d6 0%,#6fa3e3 60%,#a59a7c 100%)"></div><div class="div-label">GEOTECHNICAL DRILLING</div></div>
  <div class="card" style="left:785px;top:2405px"><div class="img" role="img" aria-label="Industrial energy plant with towers and pipework" style="background:linear-gradient(180deg,#9cc0e4 0%,#c9c2b4 40%,#5d6870 75%,#3b4249 100%)"></div><div class="div-label">RENEWABLE ENERGY SERVICES</div></div>

  <footer class="footer">
    <svg width="1200" height="467" viewBox="0 0 1200 467">
      <polygon points="0,170 302,0 1200,176 1200,467 0,467" fill="var(--red)"/>
      <polygon points="0,208 302,13 1200,203 1200,467 0,467" fill="var(--black)"/>
    </svg>
    <div class="fcol" style="left:110px">
      <h3>QUICK LINKS</h3>
      <ul><li><span class="bullet"></span>About</li><li><span class="bullet"></span>Services</li><li><span class="bullet"></span>Safety</li><li><span class="bullet"></span>Careers</li><li><span class="bullet"></span>Contact Us</li></ul>
    </div>
    <div class="fcol" style="left:322px">
      <h3>QUICK LINKS</h3>
      <ul><li><span class="bullet"></span>Site Map</li><li><span class="bullet"></span>Privacy Policy</li><li><span class="bullet"></span>Terms Of Use</li><li><span class="bullet"></span>Legal Support</li></ul>
    </div>
    <div class="fcol" style="left:553px">
      <h3>CONTACT INFO</h3>
      <div class="info"><svg viewBox="0 0 24 24"><path fill="var(--red)" d="M12 2a7 7 0 0 0-7 7c0 5 7 13 7 13s7-8 7-13a7 7 0 0 0-7-7zm0 9.5A2.5 2.5 0 1 1 12 6.5a2.5 2.5 0 0 1 0 5z"/></svg><div><b>ADDRESS:</b><span>PINE RIDGE, AB</span><span>210 Main Street T0X 1A0</span></div></div>
      <div class="info"><svg viewBox="0 0 24 24"><path fill="var(--red)" d="M6.6 10.8a15 15 0 0 0 6.6 6.6l2.2-2.2a1 1 0 0 1 1-.25 11.4 11.4 0 0 0 3.6.57 1 1 0 0 1 1 1V20a1 1 0 0 1-1 1A17 17 0 0 1 3 4a1 1 0 0 1 1-1h3.5a1 1 0 0 1 1 1c0 1.25.2 2.45.57 3.57a1 1 0 0 1-.25 1z"/></svg><div><b>PHONE:</b><span>555.014.8100</span></div></div>
      <div class="info"><svg viewBox="0 0 15 12"><rect width="15" height="12" rx="1" fill="var(--red)"/><path d="M0 1 7.5 7 15 1" stroke="#000" stroke-width="1.5" fill="none"/></svg><div><b>EMAIL:</b><span>info@marlowby.example</span></div></div>
    </div>
    <div class="fbrand">MARLOWBY</div>
    <div class="fsocial"><span class="dot red"></span><span class="dot"></span><span class="dot"></span></div>
    <div class="fline"></div>
    <div class="copy">© 2024 MARLOWBY &nbsp;|&nbsp; All Rights Reserved</div>
  </footer>

</div>
</body>
</html>
```